The Quiet Harvest Book Cover

Cover for Multiauthor Ebook & Paper Print Book Cover

Book Title:
The Quiet Harvest: Lessons of Insight From A Circle of Mentors to Guide You Toward a Fuller Journey

This book will offer the wisdom and philosophies of a variety of different coaches to allow future clients to get a taste of you and your style and prepare them to work with you!

A coach does not fix you. Or heal you. They coach you - offer thoughts to ponder, guidance, techniques to try. All to help you plays and succeed at the game of life.

Each coach has their own personality, training, experience, method and philosophy they bring to the table. The underlying purpose is to guide you through the quiet harvest, to become the person you desire and aspire to be. Different coaches for different folks, yet they all have their own unique wisdom and special sauce to share.

This book is a collection of just that. A tasting of the wisdom and philosophies of a variety of different coaches for you to experience.

Types of Coaches: Clarity, Dreams, Goals, Motivation, Mindset,  Subconscious, Beliefs, Behavior, Accountability, Life, Wellness, Love & Dating, Relationships, Sex, Business, Career,  Executive,  Personal Development,  Writing, Wellness, Fitness, Parenting,  Style, Spirituality, Public Speaking, Financial,  Time management, Weight Loss, Running, Self esteem,  Tarot, Astrology, Enneagram, Soul path/ Dharma, Skills, Performance,  Speaking / Communication, Leadership, Shadow Work, Acting, Sports, ANY & ALL

Target Market(s)

Males or females looking for guidance and words of wisdom from an expert coach - maybe to find one that resonates with them to work with further. Ages 16 and up. Any Gender. International. Looking to improve their life!

Industry/Entity Type

Self Development, Wellness, Coaching, Personal Growth, Fitness, Spirituality, Business, Relationships

Font styles to use
Serif
Script

Colors
0054AA
0677BA
7BADD7
CADEEF
E8F1F8
FFF300
FFF600
FEFA6F
FFFEC7
FFFEE8

Requirements
Must have
• I am looking for a visually appealing, unique cover that encompasses the breadth and depth of the transformation that people can go through and inspires them to want to grow and change even more. I love when elegant and classic simplicity is combined with some kind of twist that catches the eye and provokes thought. I love complimentary fonts, colors, design elements. You can visit my Brindlemart Author Page - Dr. Marisol Pendergast Voyle to see my titles to see what I have liked! But I am also excited to see where you can make my vision even better!!
Nice to have
• Front Cover - Image, Title and Subtitle, The Lantern Publishing House, Spine - Title and Publishing House Logo, Back - Book Blurb, Authors Names, Info about Publishing House, ISBN Barcode
Should not have
• Anything too feminine or too masculine as I want to encourage coaches of all genders to participate.

```html
<!DOCTYPE html>
<html lang="en">
<head>
<meta charset="utf-8">
<title>The Quiet Harvest – Cover Wrap</title>
<link href="https://fonts.googleapis.com/css2?family=Cinzel:wght@500&family=Mrs+Saint+Delafield&family=Open+Sans:wght@400&display=swap" rel="stylesheet">
<style>
  :root{
    --page:#f7f7f7;
    --paper:#ebebeb;
    --paper-edge:#dcdcdc;
    --ink:#111111;
    --blue:#0054aa;
    --blue-mid:#0677ba;
    --blue-light:#7badd7;
    --strip:#f6f6f6;
    --strip-text:#8a8a8a;
    --body-text:#222222;
  }
  *{margin:0;padding:0;box-sizing:border-box}
  html,body{width:1200px;height:1200px;overflow:hidden;background:var(--page)}
  .canvas{position:relative;width:1200px;height:1200px}
  .wrap{position:absolute;left:30px;top:190px;width:1140px;height:820px;background:var(--paper);
        display:flex;box-shadow:0 2px 10px rgba(0,0,0,.08)}
  .back{position:relative;width:545px;height:100%}
  .spine{position:relative;width:50px;height:100%;border-left:1px solid var(--paper-edge);border-right:1px solid var(--paper-edge)}
  .front{position:relative;width:545px;height:100%;overflow:hidden}

  .script{font-family:"Mrs Saint Delafield",cursive;color:var(--ink);font-weight:400;line-height:1;white-space:nowrap}
  .serif{font-family:"Cinzel",serif;color:var(--blue);font-weight:500;line-height:1;white-space:nowrap}
  .sans{font-family:"Open Sans",sans-serif;color:var(--body-text)}

  /* back cover */
  .back-butterfly{position:absolute;left:300px;top:10px;width:100px;height:95px}
  .back-title{position:absolute;left:48px;top:60px;width:290px;height:200px}
  .back-title .the{position:absolute;left:12px;top:0;font-size:52px}
  .back-title .main{position:absolute;left:0;top:78px;font-size:28px;letter-spacing:.5px}
  .back-title .end{position:absolute;left:80px;top:104px;font-size:70px}
  .back-subtitle{position:absolute;left:360px;top:118px;width:170px;font-size:13px;line-height:1.3;text-transform:uppercase}

  /* spine */
  .spine-text{position:absolute;left:50%;top:40px;transform-origin:0 0;transform:rotate(90deg) translate(0,-50%);
              white-space:nowrap;display:flex;align-items:center;gap:10px}
  .spine-text .the{font-size:30px}
  .spine-text .main{font-size:22px;letter-spacing:1px}
  .spine-text .end{font-size:36px}

  /* front cover */
  .front-title{position:absolute;left:0;top:0;width:100%;height:400px}
  .front .the{position:absolute;left:0;width:100%;top:40px;text-align:center;font-size:100px}
  .front .main{position:absolute;left:0;width:100%;top:165px;text-align:center;font-size:58px;letter-spacing:2px}
  .front .end{position:absolute;left:0;width:100%;top:255px;text-align:center;font-size:145px}
  .torn-strip{position:absolute;left:0;top:415px;width:420px;height:175px;background:var(--strip);
    clip-path:polygon(0 6%,6% 3%,12% 7%,20% 2%,28% 6%,36% 1%,45% 5%,54% 2%,63% 7%,72% 3%,82% 6%,92% 2%,100% 5%,
      100% 91%,91% 96%,81% 92%,70% 98%,60% 93%,49% 99%,38% 92%,27% 97%,17% 92%,8% 96%,0 93%);
    padding:12px 0 0 6px;overflow:hidden}
  .torn-strip p{font-family:"Open Sans",sans-serif;font-size:13px;line-height:19px;color:var(--strip-text);
    white-space:nowrap;text-transform:uppercase}
  .front-butterfly{position:absolute;left:330px;top:360px;width:210px;height:290px}
  .front-subtitle{position:absolute;left:0;width:100%;top:668px;text-align:center;font-size:18px;line-height:1.35;text-transform:uppercase;padding:0 50px}
  .publisher{position:absolute;left:0;width:100%;top:770px;text-align:center;font-size:22px;letter-spacing:.5px}
</style>
</head>
<body>
<div class="canvas">
  <div class="wrap">
    <section class="back">
      <svg class="back-butterfly" viewBox="0 0 100 95" role="img" aria-label="Illustration of a blue butterfly">
        <defs><radialGradient id="wingSmall" cx="50%" cy="50%" r="60%"><stop offset="0" stop-color="#2fd6ff"/><stop offset=".7" stop-color="#0677ba"/><stop offset="1" stop-color="#0a1f3a"/></radialGradient></defs>
        <ellipse cx="50" cy="47" rx="48" ry="44" fill="url(#wingSmall)"/>
      </svg>
      <div class="back-title">
        <span class="script the">The</span>
        <span class="serif main">QUIET</span>
        <span class="script end">Harvest</span>
      </div>
      <p class="sans back-subtitle">Lessons of insight from a circle of mentors to guide you toward a fuller journey</p>
    </section>

    <section class="spine">
      <div class="spine-text">
        <span class="script the">The</span>
        <span class="serif main">QUIET</span>
        <span class="script end">Harvest</span>
      </div>
    </section>

    <section class="front">
      <h1 class="front-title">
        <span class="script the">The</span>
        <span class="serif main">QUIET</span>
        <span class="script end">Harvest</span>
      </h1>
      <div class="torn-strip">
        <p>Clarity, Dreams, Goals, Accountability, Love &amp; Dating</p>
        <p>Business, Career, Executive, Personal Development</p>
        <p>Fitness, Parenting, Style, Spirituality, Public Speaking</p>
        <p>Management, Weight Loss, Running, Self Esteem, Tarot</p>
        <p>Enneagram, Soul Path/ Dharma, Skills, Performance</p>
        <p>Communication, Leadership, Shadow Work, Acting</p>
        <p>Goals, Motivation, Mindset, Subconscious</p>
        <p>Life, Wellness, Love, Relationships</p>
      </div>
      <svg class="front-butterfly" viewBox="0 0 210 290" role="img" aria-label="Illustration of a large blue butterfly resting on the torn strip">
        <defs><radialGradient id="wingLarge" cx="45%" cy="50%" r="60%"><stop offset="0" stop-color="#2fd6ff"/><stop offset=".65" stop-color="#0677ba"/><stop offset="1" stop-color="#0a1f3a"/></radialGradient></defs>
        <ellipse cx="110" cy="145" rx="95" ry="138" fill="url(#wingLarge)"/>
      </svg>
      <p class="sans front-subtitle">Lessons of insight from a circle of mentors to guide you toward a fuller journey</p>
      <p class="serif publisher">THE LANTERN PUBLISHING HOUSE</p>
    </section>
  </div>
</div>
</body>
</html>
```